RTavenor Business Cards & Letterhead

I have a logo but need a design for some new business cards. We are a Design-Build Firm that specializes in the design and construction of commercial projects.
the cards need to be professional. no cartoon stuff.
i would like to have the cards in AI format so I can update the card as needed. Logo is provided.
Our Address is: 4187 Marlowe Ct. Apex, North Carolina 27614

```html
<!DOCTYPE html>
<html lang="en">
<head>
<meta charset="utf-8">
<title>RTavenor Business Card</title>
<link rel="stylesheet" href="https://fonts.googleapis.com/css2?family=Montserrat:wght@400;600;800&display=swap">
<style>
  :root {
    --backdrop: #4a4a4a;
    --backdrop-dark: #383838;
    --card: #151515;
    --card-deep: #0c0c0c;
    --accent: #1565c0;
    --accent-bright: #1e7fd8;
    --ink: #ffffff;
    --emboss: #242424;
  }
  * { margin: 0; padding: 0; box-sizing: border-box; }
  html, body {
    width: 1200px; height: 801px; overflow: hidden;
    background: radial-gradient(ellipse at 40% 30%, var(--backdrop), var(--backdrop-dark));
    font-family: "Montserrat", sans-serif;
  }
  .stage {
    width: 1200px; height: 801px;
    display: flex; align-items: center; justify-content: center; gap: 40px;
  }
  .card {
    position: relative;
    width: 540px; height: 309px;
    background: var(--card);
    border-radius: 16px;
    border: 3px solid var(--accent);
    box-shadow: 0 18px 40px rgba(0,0,0,.45);
    overflow: hidden;
  }
  /* Front */
  .card-front .side-tab {
    position: absolute; left: 0; top: 170px;
    width: 10px; height: 44px; background: var(--accent-bright);
  }
  .brand {
    position: absolute; left: 40px; top: 36px;
    display: flex; align-items: center; gap: 12px;
  }
  .brand-square { width: 26px; height: 26px; background: var(--accent-bright); }
  .brand-name {
    color: var(--ink); font-weight: 800; font-size: 36px; letter-spacing: .5px;
    text-transform: uppercase; line-height: 1;
  }
  .person { position: absolute; left: 40px; top: 100px; }
  .person-name {
    color: var(--accent-bright); font-weight: 800; font-size: 19px;
    text-transform: uppercase; letter-spacing: .5px;
  }
  .person-title { color: var(--ink); font-size: 14px; margin-top: 2px; }
  .contacts { position: absolute; left: 40px; top: 168px; list-style: none; }
  .contacts li {
    display: flex; align-items: center; gap: 8px;
    color: var(--ink); font-size: 13.5px; line-height: 20px;
  }
  .contacts svg { width: 12px; height: 12px; fill: var(--accent-bright); flex: none; }
  .address {
    position: absolute; left: 40px; top: 244px;
    color: var(--ink); font-size: 13.5px; line-height: 19px; font-style: normal;
  }
  .decor-circle {
    position: absolute; right: 36px; top: 56px;
    width: 190px; height: 190px; border-radius: 50%;
    background: linear-gradient(135deg, #2c2c2c, var(--card-deep) 65%);
  }
  /* Back */
  .card-back { display: flex; align-items: center; justify-content: center; }
  .back-brand {
    display: flex; align-items: center; gap: 14px;
  }
  .back-brand .brand-square { background: var(--emboss); width: 32px; height: 32px; }
  .back-brand .brand-name { color: var(--emboss); font-size: 48px; }
</style>
</head>
<body>
<main class="stage">
  <section class="card card-front">
    <div class="side-tab"></div>
    <div class="brand">
      <span class="brand-square"></span>
      <span class="brand-name">RTavenor</span>
    </div>
    <div class="person">
      <div class="person-name">Daniel Whitcombe</div>
      <div class="person-title">Managing Director</div>
    </div>
    <ul class="contacts">
      <li><svg viewBox="0 0 24 24"><path d="M6.6 10.8a15 15 0 0 0 6.6 6.6l2.2-2.2a1 1 0 0 1 1-.25 11.4 11.4 0 0 0 3.6.57 1 1 0 0 1 1 1V20a1 1 0 0 1-1 1A17 17 0 0 1 3 4a1 1 0 0 1 1-1h3.5a1 1 0 0 1 1 1c0 1.25.2 2.45.57 3.6a1 1 0 0 1-.25 1z"/></svg>123 456 789</li>
      <li><svg viewBox="0 0 24 24"><path d="M2 5h20v14H2z M2 5l10 8 10-8" /></svg>info@yourmail.com</li>
      <li><svg viewBox="0 0 24 24"><circle cx="12" cy="12" r="10"/></svg>www.yourwebsite.com</li>
    </ul>
    <address class="address">4187 Marlowe Ct. Apex,<br>North Carolina 27614</address>
    <div class="decor-circle"></div>
  </section>
  <section class="card card-back">
    <div class="back-brand">
      <span class="brand-square"></span>
      <span class="brand-name">RTavenor</span>
    </div>
  </section>
</main>
</body>
</html>
```